Lotstallmart.com Webpage Design

Design Brief for lotstallmart.com (Copy of Brief also in attached Word file)

Name of Website- lotstallmart.com (existing logo and look & feel of website to be changed)

Logo - Finalised. The logo files are attached with the brief as “logo.jpeg”. The “Blue- Grey” version of the logo is for use on lighter backgrounds and the “Orange-White” version of the logo is for use on darker backgrounds. (A full Black version of the logo is also attached). Both versions may be used in different parts of the website. All attached files are in .png format.
Status - The website in functional and is undergoing user trials. However, we want to improve the look & feel of the website so at it seems
a. cotemporary,
b. Easy to Navigate
c. professional and
d. Vibrant.

Please visit ‘lotstallmart.com’ to check out the website and its functionalities – please use it only as a reference for the features & functions to be provided, however the designer should use a ‘Free Hand’ in designing the composition of various parts of the webpage without getting too influenced by the existing design

Objective of the Website ‘lotstallmart.com –
a. It is a portal focussed on listing of ‘Retail’ specific real-estate properties by developers, owners and realty brokers. The properties shall listed under the following four categories-
i. Retail Malls
ii. Shopping Complexes
iii. High-street shops
iv. Retail Warehouses
*refer lotstallmart.com for better clarity

b. The abovementioned properties shall be listed either for ‘Sale’ or ‘rent\lease’ or both

c. Users shall visit the site in case they wish to acquire a retail \ shop space either on ‘sale’ or ‘rent’. These Users would be able to specify the ‘Search Criteria’ through the tool-bars provided on the website – the ‘Search Criteria’ shall comprise of ‘Type of space category’, ‘City’, ‘Locality’, transaction type ie ‘Rent \ Sale’ and ‘Area Range’

d. The main revenue model for the website shall be listing fee ( or advertising charges ) payable by those listing their properties on the website.

Three Main Pages of Website (lotstallmart.com) that need to be designed -
a. Main Home Page (visit the web link - http://lotstallmart.com/ ) - The main home page has the “Search Toolbar” for specifying of Search Criteria by the User. It shall also have the following features & functions-
i. Main Advertising Banner
ii. Featured Projects
iii. New Launches
iv. Toolbar with buttons – ‘Advertise with Us’, ‘Listings Alert’, ‘Mart Wizards’, ‘Advertiser Login’

b. Property Listings Page (visit the web link - http://lotstallmart.com/gurgaon-in-india ) - The List of property options that match the Criteria specified by the ‘User’ get displayed on this page.

c. Property Detail Page - When the ‘User’ clicks on the “More….” Button on the ‘Property Listings Page’ (given in point b. above) the web page with the details of the property opens. (For Example – visit the web link - http://lotstallmart.com/vorne-Shopping-Complex-vorne-quadrion-gurgaon-636 )

Note:- Please refer to attached ‘Shopping’ related images the designer may use them on the website to provide a look & feel of retail if required – either separately or rotate in a single window

Target Market(s)

Retailers & Investors looking for retail space, Real Estate Brokers, Developers

Industry/Entity Type

Advertising

Number of Pages Required

3 page

Requirements
Must have
• Refer to existing site lotstallmart.com -- all the existing functionalities are a must have.
Nice to have
• The Designer may use the retail related images on the website if required for making it more vibrant. Refer attached images Shopping(1-6).jpg

```html
<!DOCTYPE html>
<html lang="en">
<head>
<meta charset="utf-8">
<title>Lotstallmart.com – Retail Space Portal</title>
<link href="https://fonts.googleapis.com/css2?family=Open+Sans:wght@400;600;700&family=Oswald:wght@400;500&family=Raleway:wght@400;700&display=swap" rel="stylesheet">
<style>
:root{
  --dark:#222222;
  --darker:#1b1b1b;
  --topbar:#262626;
  --orange:#e8a11c;
  --orange-btn:#d8901f;
  --blue:#0a8ee0;
  --blue-deep:#0b5d9e;
  --link:#1578c8;
  --text:#333333;
  --muted:#666666;
  --field:#eeeeee;
  --field-line:#cfcfcf;
  --white:#ffffff;
}
*{box-sizing:border-box;margin:0;padding:0}
html,body{width:1200px;height:2423px;overflow:hidden}
body{font-family:'Open Sans',Arial,sans-serif;color:var(--text);background:var(--white);position:relative}
a{text-decoration:none;color:inherit}

/* top city bar + header */
.masthead{position:absolute;left:0;top:0;width:1200px;height:170px;background:var(--dark)}
.city-bar{position:absolute;left:0;top:0;width:1200px;height:45px;border-bottom:1px solid #3a3a3a;display:flex;justify-content:center;align-items:center;gap:14px;font-size:12.5px;color:#eee}
.city-bar .sep{color:#888}
.brand{position:absolute;left:113px;top:78px;display:flex;align-items:center;gap:10px}
.brand-dot{width:34px;height:34px;border-radius:50%;background:var(--orange)}
.brand-name{font-size:34px;font-weight:700;color:var(--white);letter-spacing:-.5px}
.main-nav{position:absolute;left:441px;top:86px;display:flex;align-items:flex-start;gap:30px;color:var(--white)}
.main-nav .item{font-size:15px;line-height:20px}
.main-nav .item small{display:block;font-size:12px;color:#ddd}
.home-icon{margin-top:6px}
.advertiser{position:absolute;left:906px;top:64px;width:190px;text-align:center;color:var(--white);font-size:12.5px}
.btn-login{display:block;margin:8px auto 0;width:168px;height:41px;line-height:41px;background:var(--blue);color:var(--white);font-weight:700;font-size:15.5px;letter-spacing:.3px}
.advertiser .register{display:block;margin-top:8px;color:var(--orange);font-size:12.5px}

/* hero */
.hero-rule{position:absolute;left:0;top:170px;width:1200px;height:4px;background:var(--orange)}
.hero{position:absolute;left:0;top:174px;width:1200px;height:491px;overflow:hidden}
.hero-side{position:absolute;left:0;top:0;width:113px;height:100%;background:linear-gradient(160deg,#d8d2c8,#6b6e78 55%,#3a3f4c)}
.hero-photo{position:absolute;left:388px;top:0;width:812px;height:100%;background:linear-gradient(100deg,#f4f1ea 0%,#e9e2d4 30%,#c9b9a0 52%,#3a7fa8 62%,#b9c94e 78%,#8a6cb0 95%)}
.hero-copy{position:absolute;left:412px;top:74px;width:250px}
.hero-copy h1{font-family:'Raleway',sans-serif;font-weight:400;font-size:33px;line-height:37px;color:#222;letter-spacing:.5px}
.hero-copy h1 b{font-weight:700}
.hero-copy p{margin-top:8px;width:245px;font-size:14.5px;line-height:23px;color:#333}
.btn-blue{display:inline-block;background:var(--blue);color:var(--white);font-weight:700;font-size:15px;text-align:center}
.hero-copy .btn-blue{margin-top:14px;width:158px;height:40px;line-height:40px}

.search-panel{position:absolute;left:113px;top:0;width:273px;height:491px;background:#1d1d1d}
.search-tab{position:absolute;left:0;top:0;width:273px;height:60px}
.search-tab span{position:absolute;left:0;top:14px;width:100%;text-align:center;font-family:'Oswald',sans-serif;font-size:20px;color:var(--white);letter-spacing:.5px}
.search-form{position:absolute;left:17px;top:78px;width:240px;color:var(--white);font-size:13px}
.formats{display:grid;grid-template-columns:104px 136px;row-gap:10px;font-size:12px}
.formats label{display:flex;align-items:center;gap:8px}
.formats i{display:inline-block;width:12px;height:12px;background:var(--white)}
.field-label{display:block;margin-top:14px;margin-bottom:7px}
.formats+.field-label{margin-top:18px}
.select,.input{height:34px;background:var(--white);color:#444;font-size:12px;line-height:34px;padding:0 10px;position:relative}
.select::after{content:"";position:absolute;right:10px;top:14px;border:5px solid transparent;border-top:6px solid #222}
.btn-search{display:block;margin:16px auto 0;width:178px;height:40px;line-height:40px;background:var(--blue);text-align:center;font-weight:700;font-size:17px}

/* category bar */
.category-bar{position:absolute;left:0;top:665px;width:1200px;height:75px;background:linear-gradient(#2b2b2b,#161616);display:flex}
.category{height:75px;display:flex;align-items:center;gap:12px;color:var(--white);font-size:18px;border-right:1px solid #3c3c3c}
.category:last-child{border-right:0}
.cat-icon{width:46px;height:46px;border-radius:50%;background:var(--blue);display:flex;align-items:center;justify-content:center}

/* listing sections */
.section-title{position:absolute;left:123px;font-size:22px;font-weight:600;color:#222}
.section-rule{position:absolute;left:123px;width:954px;height:3px;background:#ddd}
.section-rule::before{content:"";position:absolute;left:0;top:0;width:38px;height:3px;background:var(--link)}
.carousel-nav{position:absolute;left:1034px;display:flex;gap:2px}
.carousel-nav span{width:20px;height:20px;border-radius:50%;background:#222;display:flex;align-items:center;justify-content:center}
.cards{position:absolute;left:123px;display:flex;gap:26px}
.card{width:218px;height:249px;background:var(--white);border:1px solid #d6d6d6;position:relative;text-align:center}
.card-img{height:120px;width:100%}
.card-city{position:absolute;right:0;top:48px;background:var(--blue);color:var(--white);font-size:15px;padding:0 10px;height:30px;line-height:30px}
.card h3{margin-top:12px;font-size:17px;font-weight:600;color:var(--link)}
.card .loc{font-size:13px;font-style:italic;color:#333;margin-top:2px}
.card .type{font-size:12.5px;color:#333;margin-top:3px}
.card .btn-view{position:absolute;left:-1px;bottom:-1px;width:218px;height:39px;line-height:39px;background:var(--orange-btn);color:var(--white);font-weight:700;font-size:15px}
.img-a{background:linear-gradient(160deg,#c9cfc4,#8c9a86 50%,#5d6b70)}
.img-b{background:linear-gradient(180deg,#1f3a6e,#4d5f88 55%,#c98b4a)}
.img-c{background:linear-gradient(180deg,#d8a78c,#b98570 45%,#7a6260)}
.img-d{background:linear-gradient(180deg,#e8a25a,#c8843a 50%,#5b4a40)}

.launches{position:absolute;left:0;top:1155px;width:1200px;height:428px;background:var(--blue-deep)}
.launches .section-title{color:var(--white)}
.launches .section-rule{background:#3d82bb}
.launches .section-rule::before{background:var(--orange)}
.launches .carousel-nav span{background:#111}

/* info columns */
.info-col{position:absolute;top:1622px;width:290px}
.info-col h2{font-size:22px;font-weight:600;color:#222;height:44px}
.info-col .rule{height:3px;background:#ddd;position:relative;margin-bottom:22px}
.info-col .rule::before{content:"";position:absolute;left:0;top:0;width:38px;height:3px;background:var(--orange)}
.info-col p{font-size:14px;line-height:22px;color:#444}
.field{height:34px;background:var(--field);border:1px solid var(--field-line);font-size:12.5px;color:#555;line-height:32px;padding:0 13px;margin-bottom:10px;position:relative}
.field.sel{color:var(--link)}
.info-col .hint{font-size:12.5px;color:#222;margin:-4px 0 12px}
.info-col .btn-blue{width:143px;height:38px;line-height:38px}
.alert-intro{display:flex;gap:16px;margin-bottom:18px;padding-left:2px}
.alert-intro p{width:212px;font-size:13.5px;line-height:21px}
.editor-img{height:102px;background:linear-gradient(180deg,#3b2e28,#8a6a4a 50%,#c7a878);margin-bottom:12px}

/* footer */
.site-footer{position:absolute;left:0;top:2038px;width:1200px;height:385px;background:#1f1f1f;color:#ddd}
.foot-col{position:absolute;top:34px}
.foot-col h2{font-size:22px;font-weight:600;color:var(--white);margin-bottom:30px}
.foot-links{display:flex;gap:48px}
.foot-links ul{list-style:none;font-size:13.5px;line-height:25px}
.foot-links li::before{content:"";display:inline-block;width:5px;height:5px;border-radius:50%;background:#ddd;margin-right:10px;vertical-align:middle}
.foot-col p{font-size:12.5px;line-height:23px}
.contact-row{display:flex;gap:12px;font-size:13px;line-height:23px;margin-bottom:16px}
.social{display:flex;gap:4px;margin-left:25px}
.social span{width:22px;height:22px;background:#2c7fd1}
.foot-bottom{position:absolute;left:121px;top:2336px;width:954px;border-top:1px solid #3a3a3a}
.copyright{position:absolute;left:121px;top:2367px;font-size:13px;color:#ddd}
.foot-brand{position:absolute;left:896px;top:2358px;display:flex;align-items:center;gap:8px}
.foot-brand .brand-dot{width:26px;height:26px}
.foot-brand .brand-name{font-size:24px}
</style>
</head>
<body>

<header class="masthead">
  <nav class="city-bar">
    <span>Bangalore</span><span class="sep">|</span><span>Chennai</span><span class="sep">|</span><span>Greater Noida</span><span class="sep">|</span><span>Gurgaon</span><span class="sep">|</span><span>Hyderabad</span><span class="sep">|</span><span>Jaipur</span><span class="sep">|</span><span>Khanna</span><span class="sep">|</span><span>Kolkatta</span><span class="sep">|</span><span>Mumbai</span><span class="sep">|</span><span>Noida</span><span class="sep">|</span><span>Pune</span><span class="sep">|</span><span>Surat</span>
  </nav>
  <a class="brand" href="http://lotstallmart.com/"><span class="brand-dot"></span><span class="brand-name">lotstallmart</span></a>
  <nav class="main-nav">
    <svg class="home-icon" width="22" height="20" viewBox="0 0 22 20"><path d="M11 1 1 10h3v9h5v-6h4v6h5v-9h3z" fill="#fff"/></svg>
    <a class="item">Advertise With Us<small>Standard listing - FREE</small></a>
    <a class="item">Mart Wizards<small>Shop Search Services</small></a>
    <a class="item" style="margin-top:10px">Listing Alerts</a>
  </nav>
  <div class="advertiser">
    Listing Your Property Here
    <a class="btn-login">ADVERTISE LOGIN</a>
    <a class="register">New Advertiser - Register</a>
  </div>
</header>

<div class="hero-rule"></div>
<section class="hero">
  <div class="hero-side" role="img" aria-label="Shopping mall interior with shoppers"></div>
  <div class="hero-photo" role="img" aria-label="Smiling couple carrying colourful shopping bags in a mall"></div>
  <div class="hero-copy">
    <h1>CORESTAGE<br>MALL <b>NOIDA</b></h1>
    <p>Lorem Ipsum is simply dummy text of the printing and typesetting industry. Lorem Ipsum has been the industry's standard dummy text ever since the 1500s.</p>
    <a class="btn-blue">LEARN MORE</a>
  </div>

  <form class="search-panel">
    <div class="search-tab">
      <svg width="273" height="60" viewBox="0 0 273 60"><path d="M0 0h273v44L136.5 60 0 44z" fill="#e8a11c"/></svg>
      <span>SELECT RETAIL FORMAT</span>
    </div>
    <div class="search-form">
      <div class="formats">
        <label><i></i>Retail Malls</label><label><i></i>Shopping Complex</label>
        <label><i></i>High Shops</label><label><i></i>Retail Warehouses</label>
      </div>
      <span class="field-label">Sale or Rent Or Both:</span>
      <div class="select">Both</div>
      <span class="field-label">Select City:</span>
      <div class="select">--Select--</div>
      <span class="field-label">Select Locality/ Micro-Market.</span>
      <div class="select">--Select--</div>
      <span class="field-label">Enter Keywords:</span>
      <div class="input">Name of Project</div>
      <a class="btn-search">SEARCH</a>
    </div>
  </form>
</section>

<nav class="category-bar">
  <a class="category" style="width:312px;padding-left:126px">
    <span class="cat-icon"><svg width="22" height="26" viewBox="0 0 22 26"><path d="M3 2h16v24H3z" fill="#fff"/><path d="M6 5h3v3H6zm7 0h3v3h-3zM6 11h3v3H6zm7 0h3v3h-3zM6 17h3v3H6zm7 0h3v3h-3z" fill="#0a8ee0"/></svg></span>Retail Malls</a>
  <a class="category" style="width:261px;padding-left:17px">
    <span class="cat-icon"><svg width="26" height="22" viewBox="0 0 26 22"><path d="M1 2h4l3 11h13l3-8H7" fill="none" stroke="#fff" stroke-width="2.5"/><circle cx="10" cy="18" r="2.3" fill="#fff"/><circle cx="19" cy="18" r="2.3" fill="#fff"/></svg></span>Shopping Complex</a>
  <a class="category" style="width:255px;padding-left:17px">
    <span class="cat-icon"><svg width="18" height="24" viewBox="0 0 18 24"><path d="M9 1a8 8 0 0 0-8 8c0 6 8 14 8 14s8-8 8-14a8 8 0 0 0-8-8z" fill="#fff"/><circle cx="9" cy="9" r="3" fill="#0a8ee0"/></svg></span>High Street Shops</a>
  <a class="category" style="width:372px;padding-left:22px">
    <span class="cat-icon"><svg width="28" height="22" viewBox="0 0 28 22"><path d="M14 1 1 11l3 3 10-8 10 8 3-3z" fill="#fff"/><path d="M6 15l8-6 8 6v6H6z" fill="#fff"/></svg></span>Retail Warehouses</a>
</nav>

<section class="featured">
  <h2 class="section-title" style="top:784px">Featured Retail Projects</h2>
  <div class="carousel-nav" style="top:792px"><span><svg width="8" height="10"><path d="M7 0 1 5l6 5z" fill="#fff"/></svg></span><span><svg width="8" height="10"><path d="M1 0l6 5-6 5z" fill="#fff"/></svg></span></div>
  <div class="section-rule" style="top:831px"></div>
  <div class="cards" style="top:861px">
    <article class="card"><div class="card-img img-a" role="img" aria-label="Aerial rendering of a shopping complex"></div><span class="card-city">Surat</span><h3>Veltara</h3><div class="loc">Althan</div><div class="type">SHOPPING COMPLEX</div><a class="btn-view">VIEW THE LISTING</a></article>
    <article class="card"><div class="card-img img-b" role="img" aria-label="High street retail tower at dusk"></div><span class="card-city">Faridabad</span><h3>Norra 81 High Street</h3><div class="loc">Sector-81</div><div class="type">SHOPPING COMPLEX</div><a class="btn-view">VIEW THE LISTING</a></article>
    <article class="card"><div class="card-img img-c" role="img" aria-label="Rendering of a retail plaza"></div><span class="card-city">Guragaon</span><h3>K4K Metropolis</h3><div class="loc">Sector-65</div><div class="type">SHOPPING COMPLEX</div><a class="btn-view">VIEW THE LISTING</a></article>
    <article class="card"><div class="card-img img-d" role="img" aria-label="Golden retail tower at sunset"></div><span class="card-city">New Delhi</span><h3>Ardent 24K</h3><div class="loc">Sohna Road</div><div class="type">SHOPPING COMPLEX</div><a class="btn-view">VIEW THE LISTING</a></article>
  </div>
</section>

<section class="launches">
  <h2 class="section-title" style="top:35px">Featured New Launches</h2>
  <div class="carousel-nav" style="top:43px"><span><svg width="8" height="10"><path d="M7 0 1 5l6 5z" fill="#fff"/></svg></span><span><svg width="8" height="10"><path d="M1 0l6 5-6 5z" fill="#fff"/></svg></span></div>
  <div class="section-rule" style="top:84px"></div>
  <div class="cards" style="top:134px">
    <article class="card"><div class="card-img img-a" role="img" aria-label="Aerial rendering of a shopping complex"></div><span class="card-city">Surat</span><h3>Veltara</h3><div class="loc">Althan</div><div class="type">SHOPPING COMPLEX</div><a class="btn-view">VIEW THE LISTING</a></article>
    <article class="card"><div class="card-img img-b" role="img" aria-label="High street retail tower at dusk"></div><span class="card-city">Faridabad</span><h3>Norra 81 High Street</h3><div class="loc">Sector-81</div><div class="type">SHOPPING COMPLEX</div><a class="btn-view">VIEW THE LISTING</a></article>
    <article class="card"><div class="card-img img-c" role="img" aria-label="Rendering of a retail plaza"></div><span class="card-city">Guragaon</span><h3>K4K Metropolis</h3><div class="loc">Sector-65</div><div class="type">SHOPPING COMPLEX</div><a class="btn-view">VIEW THE LISTING</a></article>
    <article class="card"><div class="card-img img-d" role="img" aria-label="Golden retail tower at sunset"></div><span class="card-city">New Delhi</span><h3>Ardent 24K</h3><div class="loc">Sohna Road</div><div class="type">SHOPPING COMPLEX</div><a class="btn-view">VIEW THE LISTING</a></article>
  </div>
</section>

<section class="info-col" style="left:123px">
  <h2>Listing Alert</h2><div class="rule"></div>
  <div class="alert-intro">
    <svg width="36" height="34" viewBox="0 0 36 34" style="flex:none;margin-top:4px"><path d="M2 12 18 1l16 11v21H2z" fill="#555"/><path d="M7 6h22v14H7z" fill="#fff"/><path d="M2 12l16 11 16-11" fill="none" stroke="#fff" stroke-width="2"/></svg>
    <p>Suscribe &nbsp;for Fortnightly Email update on New Listings @ Lotstallmart.com</p>
  </div>
  <div class="field">Enter your email address</div>
  <div class="field sel">Select Options</div>
  <div class="hint">(select retail format of interest)</div>
  <div class="field">Adilabad</div>
  <div class="hint">(select cities of interest)</div>
  <a class="btn-blue">SUBSCRIBE</a>
</section>

<section class="info-col" style="left:451px">
  <h2>Editor’s Choice</h2><div class="rule"></div>
  <div class="editor-img" role="img" aria-label="Shoppers with bags walking through a mall"></div>
  <p>A "Select" Listing of Retail Properties Handpicked by our Editors based on their own positive evaluation on parameters &amp; attributes such as Design Concept, Location, Developer, Success Potential. So Read On to Check Out for yourself ..........</p>
  <a class="btn-blue" style="margin-top:12px">LEARN MORE</a>
</section>

<section class="info-col" style="left:785px">
  <h2>Mart Wizards</h2><div class="rule"></div>
  <p style="margin-bottom:10px">Post your Retail Space requirement with us and our experts shall get back with suitable options and even help you in your transaction. This is a Free Service!</p>
  <div class="field">Enter your email address</div>
  <div class="field">Mobile</div>
  <div class="field" style="height:74px">Add Description of Requirement</div>
  <a class="btn-blue" style="width:84px">SEND</a>
</section>

<footer class="site-footer">
  <div class="foot-col" style="left:123px">
    <h2>About Lot Stall Mart</h2>
    <div class="foot-links">
      <ul><li>About Us</li><li>Privacy Policy</li><li>Terms of Use</li><li>Contact Us</li><li>Site Map</li></ul>
      <ul><li>Retail Malls</li><li>Shopping Complex</li><li>High Street Shops</li><li>Retail Warehouses</li></ul>
    </div>
  </div>
  <div class="foot-col" style="left:457px;width:312px">
    <h2>Who We Are</h2>
    <p>Lotstallmart.com is a Specialised Web based platform for Retail Space, featuring properties across India under various formats such as Retail Malls, Shopping Complexes, High-street Shops. Also featured are Retail Warehouses which provide the logistic back-end for the retail business. Lotstallmart.com is useful to various category of users as follows- a. Devel <span style="color:var(--blue)">More...</span></p>
  </div>
  <div class="foot-col" style="left:815px;width:270px">
    <h2>Contact Us</h2>
    <div class="contact-row"><svg width="14" height="20" viewBox="0 0 14 20" style="flex:none"><path d="M7 0a7 7 0 0 0-7 7c0 5 7 13 7 13s7-8 7-13a7 7 0 0 0-7-7z" fill="#e8a11c"/><circle cx="7" cy="7" r="2.5" fill="#1f1f1f"/></svg><span>Retail Plaza Suite 18, 2nd Floor,<br>Lorem Ipsum is simply,<br>Sector-x, Gurgaon - 100000</span></div>
    <div class="contact-row" style="margin-bottom:6px"><svg width="14" height="16" viewBox="0 0 14 16"><path d="M3 1l3 3-2 2c1 2 3 4 5 5l2-2 3 3-2 3C6 15 0 8 1 3z" fill="#e8a11c"/></svg><span>Phone : 000-000-0000</span></div>
    <div class="contact-row" style="margin-bottom:10px"><svg width="16" height="14" viewBox="0 0 16 14"><path d="M3 0h8v4H3zM0 5h16v7H0zM4 9h8v5H4z" fill="#e8a11c"/></svg><span>Fax : 000 - 000 - 0000</span></div>
    <div class="social"><span></span><span></span><span style="background:#c8372d"></span><span style="background:#555"></span><span></span></div>
  </div>
</footer>
<div class="foot-bottom"></div>
<div class="copyright">Copyright © 2015 Lot Stall Mart. All rights reserved.</div>
<div class="foot-brand"><span class="brand-dot"></span><span class="brand-name">lotstallmart</span></div>

</body>
</html>
```